Homemaking training schools needs a Business Card design

Designer, Hello!

No special requirements, good-looking enough.
--------------------------------------------------------------------------

Name: Marcus Dole
Chairman
Tel: 0574-71948263
Mobile: 13857420916
Email: kelvora@mailnest.example
Web: www.prt2019.example
Add: No.258, LanpingJie, BeiyuanQu, Ningbo, Zhejiang

LOGO
Ningbo PRT Homemaking Training School

Target Market(s)

pregnant women, mothers, infants, the elderly and families, including cleaning, cooking, nursing training.

Industry/Entity Type

Business

Contact Information for Business Card

Name: Marcus Dole
Chairman
Tel: 0574-71948263
Mobile: 13857420916
Email: kelvora@mailnest.example
Web: www.prt2019.example

LOGO

Font styles to use
Serif
Sans Serif
Decorative

Requirements
Nice to have
• Feels: clean, specifications, safety, comfort, warmth and happiness.

```html
<!DOCTYPE html>
<html lang="en">
<head>
<meta charset="utf-8">
<title>PeiRongTai Business Card</title>
<link rel="stylesheet" href="https://fonts.googleapis.com/css2?family=Montserrat:wght@400;500;600;700&display=swap">
<style>
  :root {
    --bg: #2a2a2a;
    --card-dark: #3c3c3c;
    --card-light: #ffffff;
    --blue: #1b72bf;
    --pink: #e6007e;
    --ink: #333333;
    --grey: #8a8a8a;
    --white: #ffffff;
  }
  * { box-sizing: border-box; margin: 0; padding: 0; }
  html, body { width: 1200px; height: 900px; overflow: hidden; }
  body {
    background: var(--bg);
    font-family: "Montserrat", Arial, sans-serif;
    position: relative;
  }
  .card {
    position: absolute;
    width: 620px;
    height: 354px;
    border-radius: 2px;
    box-shadow: 0 12px 30px rgba(0,0,0,.45);
    overflow: hidden;
  }

  /* Back side */
  .card-back {
    left: 90px; top: 70px;
    background: var(--card-dark);
  }
  .back-brand {
    position: absolute;
    left: 0; right: 0; top: 130px;
    display: flex; align-items: center; justify-content: center; gap: 14px;
  }
  .back-brand .dot {
    width: 30px; height: 30px; border-radius: 50%;
    background: var(--pink);
  }
  .back-brand .name {
    font-size: 40px; font-weight: 600; color: var(--white);
    letter-spacing: .5px;
  }
  .back-url {
    position: absolute;
    left: 0; right: 0; bottom: 34px;
    text-align: center;
    color: var(--white);
    font-size: 19px; font-weight: 600;
    letter-spacing: .5px;
  }

  /* Front side */
  .card-front {
    left: 490px; top: 470px;
    background: var(--card-light);
  }
  .brand {
    position: absolute;
    left: 40px; top: 120px;
    width: 290px;
  }
  .brand-name {
    display: flex; align-items: center; gap: 10px;
  }
  .brand-name .dot {
    width: 16px; height: 16px; border-radius: 50%;
    background: var(--pink); flex: none;
  }
  .brand-name .name {
    font-size: 34px; font-weight: 600; color: var(--blue);
  }
  .tagline {
    display: flex; align-items: center; gap: 10px;
    margin-top: 6px;
    color: var(--grey);
    font-size: 14px; font-weight: 400;
    letter-spacing: .5px;
  }
  .tagline::before, .tagline::after {
    content: ""; flex: 1; height: 1px; background: var(--ink);
  }
  .divider {
    position: absolute;
    left: 352px; top: 62px;
    width: 1px; height: 170px;
    background: var(--blue);
  }
  .contact {
    position: absolute;
    left: 374px; top: 58px;
    width: 236px;
    color: var(--blue);
  }
  .person-name {
    font-size: 25px; font-weight: 700; letter-spacing: .5px;
    line-height: 1.05;
  }
  .person-title {
    font-size: 11px; font-weight: 600; color: var(--ink);
    letter-spacing: 1px; margin-bottom: 6px;
  }
  .address {
    font-size: 12.5px; font-weight: 500; line-height: 1.35;
    margin-bottom: 4px;
  }
  .contact-list { list-style: none; }
  .contact-list li {
    display: flex; align-items: center; gap: 8px;
    font-size: 12.5px; font-weight: 500; line-height: 1.45;
  }
  .contact-list svg { width: 11px; height: 11px; flex: none; }
  .school-line {
    position: absolute;
    left: 0; right: 0; bottom: 30px;
    text-align: center;
    font-size: 13px; font-weight: 600;
    color: var(--ink);
    letter-spacing: .6px;
  }
</style>
</head>
<body>

<section class="card card-back">
  <div class="back-brand">
    <span class="dot"></span>
    <span class="name">PeiRongTai</span>
  </div>
  <p class="back-url">www.prt2019.example</p>
</section>

<section class="card card-front">
  <div class="brand">
    <div class="brand-name">
      <span class="dot"></span>
      <span class="name">PeiRongTai</span>
    </div>
    <div class="tagline">Training &amp; Services</div>
  </div>

  <div class="divider"></div>

  <div class="contact">
    <h1 class="person-name">MARCUS DOLE</h1>
    <p class="person-title">CHAIRMAN</p>
    <p class="address">258, LanpingJie<br>BeiyuanQu, Ningbo, Zhejiang</p>
    <ul class="contact-list">
      <li>
        <svg viewBox="0 0 24 24" aria-hidden="true"><path fill="#333" d="M6.6 10.8a15.1 15.1 0 0 0 6.6 6.6l2.2-2.2c.3-.3.7-.4 1-.2 1.1.4 2.3.6 3.6.6.6 0 1 .4 1 1V20c0 .6-.4 1-1 1A17 17 0 0 1 3 4c0-.6.4-1 1-1h3.5c.6 0 1 .4 1 1 0 1.3.2 2.5.6 3.6.1.3 0 .7-.2 1z"/></svg>
        0574-71948263
      </li>
      <li>
        <svg viewBox="0 0 24 24" aria-hidden="true"><rect x="6" y="2" width="12" height="20" rx="2" fill="none" stroke="#333" stroke-width="2.4"/><circle cx="12" cy="18" r="1.3" fill="#333"/></svg>
        13857420916
      </li>
      <li>
        <svg viewBox="0 0 24 24" aria-hidden="true"><rect x="2" y="5" width="20" height="14" rx="1.5" fill="none" stroke="#333" stroke-width="2.2"/><path d="M2.5 6l9.5 7 9.5-7" fill="none" stroke="#333" stroke-width="2.2"/></svg>
        kelvora@mailnest.example
      </li>
      <li>
        <svg viewBox="0 0 24 24" aria-hidden="true"><circle cx="12" cy="12" r="10" fill="none" stroke="#333" stroke-width="2"/><path d="M2 12h20M12 2c3 3 3 17 0 20M12 2c-3 3-3 17 0 20" fill="none" stroke="#333" stroke-width="1.6"/></svg>
        www.prt2019.example
      </li>
    </ul>
  </div>

  <p class="school-line">NINGBO PRT HOMEMAKING TRAINING SCHOOL</p>
</section>

</body>
</html>
```